Wordpress Theme for Harbourview Clinics

** Please view updated Sitemap2.pdf doc to clarify some confusion ***

This is a multiuser WordPress subscription site for Harbourview Clinics. Please see attachment for sitemap. Please do not include extra content like social media icons, search bars, or images. If you have questions, please ask for clarification.
The site contains the following pages and sub-pages:

1. Home
2. Our Clinic
2a. Our Clinic > Mission
2b. Our Clinic > Services
2c. Our Clinic > Clinic Policies
2d. Our Clinic > Schedules
3. Our Staff
3a. Our Staff > [Staff member page]
4. Resources
4a. Resources > Patient Health (index)
4b. Resources > Patient Health (index) > [post]
4c. Resources > Links
4d. Resources > Forms
5. Alerts
5a. Alerts > [Alert Page]
6. Contact Us

Includes the Following Pages, Subpages, and Content
1. Home
a. About Us
b. Our Staff
c. Bulletins
d. Accepting New Patients (shown as an alert widget)
e. Links
i. Physician Toolbox
ii. Book an Appointment
f. Clinic Policies
i. Show first 3 policies (e.g. Late Arrivals, Missed Appointments, Fees)
ii. Link to Clinic Policies page
g. Primary widget (displayed on all pages)
i. Hours of operation
ii. Contact Info
1. Tel
2. Fax
3. Email
4. Address
5. Get directions (link to Google Maps)
2. Our Clinic
a. Main Page
i. Clinic Name
ii. Overview
iii. Languages Spoken
iv. Secondary Navigation
1. Mission
2. Services
3. Clinic Policies
4. Schedules (see attachment)
b. Our Clinic > Mission
c. Our Clinic > Services
i. For each service include service TITLE and DESCRIPTION
d. Our Clinic > Clinic Policies
i. For each policy include policy TITLE and DESCRIPTION
ii. Include the following policies in mockup
1. Late arrivals
2. Missed appointments
3. Fees for missed appointments
4. Referrals and follow-ups
5. Services not covered by RDA
6. Information for LTF patients
7. Medical Legal Reports
e. Our Clinic > Schedules
3. Our Staff
a. Main Page
i. Display a list of staff members. Include NAME and DESIGNATION
b. Our Staff > [Staff Name]
i. Include NAME, PICTURE, DESIGNATION, and BIO
4. Resources
a. Resources > Patient Health
i. Main Page
1. Posts (ordered by date)
a. Title
b. Summary
2. Side Navigation
a. Post Categories
ii. Patient Health > [post title]
1. Title
2. Post Category
3. Date
4. Author
5. Summary
6. Body
b. Resources > Links
1. Secondary Navigation - Categories
a. Sample Categories:
i. Local Services
ii. RDA and Drug Coverage
iii. Mental Health Resources
2. Category page
a. Include the following links in the 'Local Services' category
i. Hypertension clinics
ii. Home Care services
iii. Vaccine Clinics
c. Resources > Forms
i. Display a table with form TITLE and CATEGORY
ii. Side Navigation
1. Form Categories
a. Use the following sample Categories
i. Referrals
ii. Insurance
iii. Intake
iv. Discharge
v. Waivers
5. Alerts
a. Main page
i. List of all Alert posts
1. Include post TITLE as a link to the post
ii. Side Navigation
1. Alerts Archive
a. shown as Month + Number of posts
iii. Alerts > [Alert page]
1. Include TITLE, DATE, AUTHOR, BODY
6. Contact Us
a. Map
b. Hours of operation
c. Address
d. Phone number
e. Fax number
e. Fax number
f. Map
g. Email

Design notes:
- fixed width
- responsive (need designs for mobile, tablet, and desktop)
- simple, dark font, white background
- use Font Awesome icons where needed
- user adds own logo

Target Market(s)

Harbourview Clinics

Industry/Entity Type

Medical

Number of Pages Required

5+ page

Font styles to use
Serif
Sans Serif

Requirements
Must have
• Please keep designs very simple.
• Examples:
• https://www.quolbin.com/install
• http://www.ventrohax.com/company/about-us
• http://brindlequota.org/
• http://www.trosk.com/
Should not have
• Minimal or no use of shadows and gradients

```html
<!DOCTYPE html>
<html lang="en">
<head>
<meta charset="utf-8">
<title>Our Staff – Harbourview Clinics</title>
<link href="https://fonts.googleapis.com/css2?family=Open+Sans:wght@400;600;700&family=Raleway:wght@500&family=Lato:wght@400&display=swap" rel="stylesheet">
<style>
:root{
  --blue:#0a8be0;
  --blue-dark:#0573c2;
  --ink:#222;
  --text:#333;
  --band:#f7f7f7;
  --footer:#252525;
  --footer-line:#3a3a3a;
  --footer-text:#8a8a8a;
  --footer-head:#9a9a9a;
  --white:#fff;
}
*{margin:0;padding:0;box-sizing:border-box}
html,body{width:1200px;height:782px;overflow:hidden;background:var(--white)}
body{font-family:"Open Sans",Arial,sans-serif;color:var(--text);position:relative}
a{color:inherit;text-decoration:none}

.topbar{position:absolute;left:0;top:0;width:1200px;height:30px;background:var(--blue);color:var(--white);font-size:10px;font-family:"Lato",Arial,sans-serif}
.topbar .contact{position:absolute;left:161px;top:9px;display:flex}
.topbar .actions{position:absolute;right:161px;top:9px;display:flex}
.topbar span+span{border-left:1px solid var(--white);margin-left:5px;padding-left:5px}

.header{position:absolute;left:0;top:30px;width:1200px;height:83px}
.brand{position:absolute;left:162px;top:26px;display:flex;align-items:center;gap:14px}
.brand .dot{width:30px;height:30px;border-radius:50%;background:var(--blue)}
.brand .name{font-family:"Raleway",Arial,sans-serif;font-weight:500;font-size:21px;color:var(--ink)}
.nav{position:absolute;left:554px;top:0;height:83px;display:flex;font-family:"Lato",Arial,sans-serif;font-size:11px;color:var(--ink)}
.nav a{display:flex;align-items:center;justify-content:center;height:83px;padding:0 16px}
.nav a.active{background:var(--blue-dark);color:var(--white);padding:0 8px;width:60px;margin:0 10px}

.page-band{position:absolute;left:0;top:113px;width:1200px;height:59px;background:var(--band)}
.page-band h1{position:absolute;left:162px;top:16px;font-size:10px;font-weight:700;color:var(--ink)}
.page-band .crumbs{position:absolute;left:162px;top:35px;font-size:10px;color:var(--ink)}

.staff-photo{position:absolute;left:161px;top:210px;width:428px;height:300px;background:linear-gradient(#f6f6f6,#ededed);border-bottom:4px solid var(--blue)}
.staff-info{position:absolute;left:610px;top:207px;width:429px;color:var(--ink)}
.staff-info h2{font-size:12.5px;font-weight:700}
.staff-info .rule{width:114px;height:1px;background:#bbb;margin:9px 0 10px}
.staff-info .role{font-size:9.5px;font-weight:700}
.staff-info .bio{font-size:9.8px;line-height:15px;text-align:justify;margin-top:16px}
.staff-info h3{font-size:9.5px;font-weight:700;margin-top:26px}
.staff-info .hours{font-size:9.8px;margin-top:10px}

.footer{position:absolute;left:0;top:555px;width:1200px;height:227px;background:var(--footer);border-top:4px solid var(--blue)}
.footer .brand{left:162px;top:37px}
.footer .brand .name{color:var(--white)}
.footer .about{position:absolute;left:162px;top:84px;width:205px;font-size:9px;line-height:13.5px;color:#ddd}
.fcol{position:absolute;top:33px;font-size:10px;color:var(--footer-text)}
.fcol h4{font-size:12.5px;font-weight:600;color:var(--footer-head);margin-bottom:7px}
.fcol li{list-style:none;line-height:18px}
.fcol li.current{color:#ddd}
.fcol.nav-col{left:461px}
.fcol.links-col{left:686px}
.fcol.contact-col{left:836px;top:32px}
.contact-col dl{display:grid;grid-template-columns:90px 1fr;line-height:15px;padding-left:2px}
.footer .bottom{position:absolute;left:0;top:187px;width:1200px;height:36px;border-top:1px solid var(--footer-line);font-size:10px;color:var(--footer-text)}
.bottom .copy{position:absolute;left:162px;top:10px}
.bottom .legal{position:absolute;left:463px;top:10px;display:flex;gap:25px}
</style>
</head>
<body>
<div class="topbar">
  <div class="contact"><span>To help Here : 204 318 7450</span><span>Email : hello@harbourview.ca</span></div>
  <div class="actions"><span>Book an Appointment</span><span>Physician Toolbox</span></div>
</div>

<header class="header">
  <a class="brand" href="#"><span class="dot"></span><span class="name">Harbourview Clinics</span></a>
  <nav class="nav">
    <a href="#">Home</a><a href="#">Our Clinic</a><a href="#">Newsletter</a><a class="active" href="#">Our Staff</a><a href="#">Resources</a><a href="#">Contact Us</a>
  </nav>
</header>

<section class="page-band">
  <h1>OUR STAFF</h1>
  <p class="crumbs">HOME / OUR STAFF/STAFF-MEMBER</p>
</section>

<main>
  <div class="staff-photo" role="img" aria-label="Portrait photo of the pediatrist in a white coat with a stethoscope"></div>
  <article class="staff-info">
    <h2>Dr. Elena Marsh</h2>
    <div class="rule"></div>
    <p class="role">PEDIATRIST</p>
    <p class="bio">Contrary to popular belief, Lorem Ipsum is not simply random text. It has roots in a piece of classical Latin literature from 45 BC, making it over 2000 years old. Tomas Verhoef, a Latin professor at Linwood-Carrow College in Virginia, looked up one of the more obscure Latin words, consectetur, from a Lorem Ipsum passage, and going through the cites of the word in classical literature.</p>
    <h3>Office Hours</h3>
    <p class="hours">Monday, Thursday, Friday</p>
  </article>
</main>

<footer class="footer">
  <div class="brand"><span class="dot"></span><span class="name">Harbourview Clinics</span></div>
  <p class="about">Lorem Ipsum is simply dummy text of the printing and typesetting industry. Lorem Ipsum has been the industry's standard dummy text</p>
  <div class="fcol nav-col"><h4>Navigation</h4><ul><li class="current">Home</li><li>Our Clinic</li><li>Newsletter</li><li>Our Staff</li><li>Resources</li></ul></div>
  <div class="fcol links-col"><h4>Links</h4><ul><li>Help</li><li>Support</li><li>Privacy Policy</li></ul></div>
  <div class="fcol contact-col"><h4>Contact Us</h4>
    <dl><dt>Telephone :</dt><dd>204-318-7451</dd><dt>Email:</dt><dd>hello@harbourview.ca</dd><dt>Address:</dt><dd>48 Alder Row<br>Northgate, B. Canada,<br>V2K 4PL</dd></dl>
  </div>
  <div class="bottom">
    <span class="copy">© 2015 Harbourview Clinics. All Rights Reserved</span>
    <span class="legal"><a href="#">About Us</a><a href="#">Terms of Use</a><a href="#">Privacy Policy</a></span>
  </div>
</footer>
</body>
</html>
```